Business Intelligence Application - Reporting Menu and Report Criteria Design

Looking for a fresh, effective and user friendly view for the menu structure and reporting criteria screen format for a business reporting application. Initial format completed, content structure is in place, but we need the 'wow' design.. as its a serious professional report/BI tool it has to fall within certain guidelines for clarity and graphics..but we want it to be slick, friendly, great user experience. There is a large amount of complex content to fit into a small space and we need it to be very inviting, modern and intuitive.. If interested, please review the attachment. We have live screens in operation, but feel these could be improved and looking forward to seeing what great creative suggestions could be made. Please review work done to date in the attached.. We are not looking for a total re-design of everything, all the basic business content/structure is there.. but tell us what we could do to improve this in terms of graphic design... particularly the criteria screens.. thanks!
Updates

Reason: Need a few more days to review designs - thanks for all submissions so far, we will make a selection shortly.

Target Market(s)

Business analysts, hotel operations teams, finance analysts hospitality industry

Industry/Entity Type

Hospitality

Coding

Coded - Design and coding required

Number of Pages Required

4 page

Font styles to use
Sans Serif
Other font styles liked:
• Candara, please see example in deck

Colors
3276b5
3176b5
0255a3
85acd3
33a6d7
cee9f5
85cae6

Requirements
Must have
• sharp clear, logical menu structure, (currently it has 'clicks to sub-menus, we need hover over, slide to sub-menus..) colour, styling.. and most focus on revision of criteria.. right now is somewhat heavy, cumbersome.. keep colour and friendly intuitive process steps.. its heavy analytical stuff.. best of luck!
Should not have
• No grey fonts on white or grey screens! many business apps are not readable or sharp.. or fonts are too small.. colourless, so please avoid that.. see our deck - sharp dark (navy) or black fonts on white, or light shading..

```html
<!DOCTYPE html>
<html lang="en">
<head>
<meta charset="utf-8">
<title>Amber Crest Hotel &amp; Residences – Property Search</title>
<link href="https://fonts.googleapis.com/css2?family=PT+Sans:wght@400;700&display=swap" rel="stylesheet">
<style>
  :root {
    --brand-blue: #33a6d7;
    --band-blue: #cee9f5;
    --hover-blue: #85cae6;
    --divider: #5bb9e1;
    --ink: #0f1a2a;
    --ink-soft: #1e2a3a;
    --white: #ffffff;
    --field-border: #9aa3ad;
  }
  * { box-sizing: border-box; margin: 0; padding: 0; }
  html, body { width: 1200px; height: 508px; overflow: hidden; background: var(--white); }
  body { font-family: "PT Sans", sans-serif; color: var(--ink); position: relative; }

  .top-bar { position: absolute; left: 0; top: 0; width: 1200px; height: 60px; background: var(--band-blue); }
  .brand { position: absolute; left: 48px; top: 15px; display: flex; align-items: center; gap: 9px; }
  .brand-dot { width: 30px; height: 30px; border-radius: 50%; background: var(--brand-blue); }
  .brand-name { font-size: 19px; font-weight: 700; color: var(--brand-blue); letter-spacing: -0.2px; }

  .session-info { position: absolute; top: 21px; font-size: 13px; font-weight: 700; color: var(--ink); }
  .session-user { left: 556px; }
  .session-date { left: 668px; }

  .app-switch { position: absolute; top: 11px; width: 107px; height: 37px; background: var(--brand-blue);
    color: var(--white); font-size: 12px; font-weight: 700; letter-spacing: 0.4px;
    display: flex; align-items: center; justify-content: center; border-radius: 2px; }
  .app-switch.intel { left: 834px; }
  .app-switch.planning { left: 956px; }

  .header-icon { position: absolute; top: 17px; width: 26px; height: 26px; }
  .icon-alerts { left: 1084px; }
  .icon-share { left: 1125px; }

  .main-nav { position: absolute; left: 47px; top: 89px; display: flex; align-items: center; font-size: 13px; font-weight: 700; color: var(--ink); }
  .main-nav .sep { width: 3px; height: 3px; border-radius: 50%; background: var(--brand-blue); margin: 0 9px; }

  .property-search { position: absolute; left: 775px; top: 81px; width: 373px; height: 37px;
    border: 1px solid var(--field-border); border-radius: 2px; background: var(--white);
    display: flex; align-items: center; padding: 0 14px 0 17px; justify-content: space-between;
    font-size: 11.5px; color: var(--ink-soft); letter-spacing: 0.2px; }

  .menu-caret { position: absolute; left: 784px; top: 133px; width: 0; height: 0;
    border-left: 8px solid transparent; border-right: 8px solid transparent; border-bottom: 8px solid var(--brand-blue); }

  .search-menu { position: absolute; list-style: none; background: var(--brand-blue);
    box-shadow: 0 2px 6px rgba(0,0,0,0.12); border-radius: 1px; }
  .search-menu li { height: 34px; display: flex; align-items: center; justify-content: space-between;
    padding: 0 13px 0 11px; color: var(--white); font-size: 11.5px; border-bottom: 1px solid var(--divider); }
  .search-menu li:last-child { border-bottom: none; }
  .search-menu li.is-active { background: var(--hover-blue); }
  .criteria-menu { left: 775px; top: 141px; width: 163px; }
  .region-menu { left: 938px; top: 242px; width: 164px; }
  .region-menu li { padding-left: 14px; height: 33.6px; }
  .region-menu li.group-open { height: 31px; border-bottom: none; }
  .region-menu li:last-child { height: 37px; padding-bottom: 4px; }
  .arrow-right { width: 0; height: 0; border-top: 4px solid transparent; border-bottom: 4px solid transparent; border-left: 5px solid var(--white); }
  .arrow-down { width: 0; height: 0; border-left: 4.5px solid transparent; border-right: 4.5px solid transparent; border-top: 5px solid var(--white); }
</style>
</head>
<body>
  <header class="top-bar">
    <div class="brand"><span class="brand-dot"></span><span class="brand-name">Amber Crest Hotel &amp; Residences</span></div>
    <span class="session-info session-user">Welcome Admin</span>
    <span class="session-info session-date">Tuesday October 04.2017</span>
    <span class="app-switch intel">INTEL</span>
    <span class="app-switch planning">PLANNING</span>
    <svg class="header-icon icon-alerts" viewBox="0 0 26 26" fill="none" stroke="#1e2a3a" stroke-width="1.2" aria-label="Alerts" role="img">
      <path d="M8 18V12a5 5 0 0 1 10 0v6l1.5 2h-13z"/>
      <path d="M11.5 22a1.6 1.6 0 0 0 3 0"/>
      <path d="M13 5v2"/>
      <path d="M4.5 10c-1 1.5-1 4 0 5.5M21.5 10c1 1.5 1 4 0 5.5"/>
    </svg>
    <svg class="header-icon icon-share" viewBox="0 0 26 26" fill="none" stroke="#1e2a3a" stroke-width="1.3" aria-label="Share" role="img">
      <path d="M18 9H5v13h16v-5"/>
      <path d="M9 17c1-5 5-7.5 10-7.5V6.5l5 4.5-5 4.5v-3c-4 0-7.5 1.5-10 4.5z"/>
    </svg>
  </header>

  <nav class="main-nav">
    <span>Admin</span><span class="sep"></span>
    <span>Management</span><span class="sep"></span>
    <span>Rooms Performance</span><span class="sep"></span>
    <span>Revenue Summary</span><span class="sep"></span>
    <span>Demand &amp; Risk</span><span class="sep"></span>
    <span>Inventory Analysis</span><span class="sep"></span>
    <span>Placeholder</span>
  </nav>

  <div class="property-search">
    <span>PROPERTY SEARCH</span>
    <svg width="14" height="14" viewBox="0 0 14 14" fill="none" stroke="#1e2a3a" stroke-width="1.3" aria-hidden="true">
      <circle cx="6" cy="6" r="4.6"/><path d="M9.4 9.4L13 13"/>
    </svg>
  </div>

  <span class="menu-caret"></span>
  <ul class="search-menu criteria-menu">
    <li>Property Name <span class="arrow-right"></span></li>
    <li>Property ID</li>
    <li>Product Type</li>
    <li class="is-active">Europe <span class="arrow-right"></span></li>
    <li>All Region</li>
    <li>All Area</li>
  </ul>

  <ul class="search-menu region-menu">
    <li>UK &amp; Ireland</li>
    <li class="group-open">Central London <span class="arrow-down"></span></li>
    <li>Regent Row Hotel</li>
    <li>Grand Regent Row Hotel</li>
    <li>Southbank Quay Hotel</li>
    <li>Riverside Arch Hotel</li>
  </ul>
</body>
</html>
```